Lumavento business card

We need a modern business card - With our 4 colors - See web: www.lumavento.dk

I have attached logo and som old business Cards we have - Lets Make the new ones shine...:-) -

Industry/Entity Type

Business

Requirements
Must have
• the logo with lumavento only,

```html
<!DOCTYPE html>
<html lang="da">
<head>
<meta charset="utf-8">
<title>Lumavento – visitkort</title>
<link href="https://fonts.googleapis.com/css2?family=Source+Sans+3:wght@400;600&display=swap" rel="stylesheet">
<style>
  :root {
    --backdrop: #3a3331;
    --card: #141414;
    --card-back: #111111;
    --emboss: #3c3c3c;
    --green: #8cd63c;
    --purple: #7b2f8e;
    --magenta: #d42f8c;
    --orange: #f0932b;
    --text: #f2a531;
  }
  * { box-sizing: border-box; margin: 0; padding: 0; }
  html, body {
    width: 1200px; height: 814px; overflow: hidden;
    background: var(--backdrop);
    font-family: "Source Sans 3", sans-serif;
  }
  .stage {
    width: 1200px; height: 814px;
    display: flex; align-items: center; justify-content: center; gap: 40px;
  }
  .card {
    position: relative;
    width: 540px; height: 310px;
    border-radius: 3px;
    overflow: hidden;
  }
  /* Back side */
  .card--back { background: var(--card-back); display: flex; align-items: center; justify-content: center; }
  .brand-mark { display: flex; align-items: center; gap: 14px; }
  .brand-dot { width: 26px; height: 26px; border-radius: 50%; background: var(--emboss); }
  .brand-name {
    font-size: 44px; font-weight: 400; letter-spacing: 3px;
    color: var(--emboss);
  }
  /* Front side */
  .card--front { background: var(--card); }
  .identity {
    position: absolute; left: 34px; top: 78px; width: 230px;
    text-align: center;
  }
  .identity .logo { display: flex; align-items: center; justify-content: center; gap: 8px; margin-bottom: 12px; }
  .identity .logo-dot { width: 14px; height: 14px; border-radius: 50%; background: var(--green); }
  .identity .logo-name { font-size: 26px; font-weight: 400; color: var(--green); letter-spacing: 1px; }
  .person-name { font-size: 21px; font-weight: 600; color: var(--text); }
  .rule { height: 2px; background: var(--green); margin: 3px 0 6px; }
  .person-role { font-size: 14px; color: var(--text); }
  .contact {
    position: absolute; left: 300px; top: 82px;
    font-size: 15px; line-height: 20px; color: var(--text);
    list-style: none;
  }
  .contact .address { margin-bottom: 2px; }
  .contact li { display: flex; align-items: center; gap: 8px; }
  .contact svg { width: 13px; height: 13px; flex: none; }
  .contact .no-icon { padding-left: 21px; }
  .color-bands { position: absolute; left: 0; right: 0; bottom: 0; height: 16px; display: flex; }
  .color-bands span { flex: 1; }
  .band-green { background: var(--green); }
  .band-purple { background: var(--purple); }
  .band-magenta { background: var(--magenta); }
  .band-orange { background: var(--orange); }
</style>
</head>
<body>
<main class="stage">
  <section class="card card--back" aria-label="Bagside">
    <div class="brand-mark">
      <span class="brand-dot"></span>
      <span class="brand-name">lumavento</span>
    </div>
  </section>

  <section class="card card--front" aria-label="Forside">
    <div class="identity">
      <div class="logo"><span class="logo-dot"></span><span class="logo-name">lumavento</span></div>
      <p class="person-name">Maren Holmgaard</p>
      <div class="rule"></div>
      <p class="person-role">CEO - Direktør</p>
    </div>

    <ul class="contact">
      <li class="no-icon">Lyngbakken 12</li>
      <li class="no-icon address">2800 Kongens Lyngby</li>
      <li>
        <svg viewBox="0 0 16 16"><path fill="#8cd63c" d="M3.5 1l2.5 3-1.5 2c1 2 2.5 3.5 4.5 4.5l2-1.5 3 2.5-1.5 2.5C7 14 2 9 1 2.5z"/></svg>
        +45 31 24 67 80
      </li>
      <li>
        <svg viewBox="0 0 16 16"><path fill="#8cd63c" d="M3.5 1l2.5 3-1.5 2c1 2 2.5 3.5 4.5 4.5l2-1.5 3 2.5-1.5 2.5C7 14 2 9 1 2.5z"/></svg>
        +45 52 73 19 46
      </li>
      <li>
        <svg viewBox="0 0 16 16"><rect x="1" y="3" width="14" height="10" fill="#8cd63c"/><path d="M1 3l7 6 7-6" fill="none" stroke="#141414" stroke-width="1.4"/></svg>
        mh@lumavento.dk
      </li>
      <li>
        <svg viewBox="0 0 16 16"><circle cx="8" cy="8" r="7" fill="#8cd63c"/><path d="M1 8h14M8 1c-3 3-3 11 0 14M8 1c3 3 3 11 0 14" fill="none" stroke="#141414" stroke-width="1.2"/></svg>
        www.lumavento.dk
      </li>
    </ul>

    <div class="color-bands">
      <span class="band-green"></span>
      <span class="band-purple"></span>
      <span class="band-magenta"></span>
      <span class="band-orange"></span>
    </div>
  </section>
</main>
</body>
</html>
```